Varnik Holdings — Business Card Design Brief
Overview
Design a double-sided business card for Varnik Holdings that highlights our two service arms: Varnik Communications (telecommunications) and Varnik Energy (business energy solutions). The card should feel smart and stand out when handed to clients.

Objectives
Showcase our areas of specialty clearly.
Reflect the overall Varnik / Varnik Holdings brand while acknowledging both arms.
Explore using both logos (Communications + Energy) or one unified logo, depending on the design.

Deliverables
One double-sided business card design (front + back).

Content & Copy
Front (preferred): Logo: Varnik / Varnik Holdings
Descriptor: Business Communications | Business Energy
Back:My contact details and company details
Core products: Business Mobile • Telephony • Internet • Business Energy Solutions

Brand & Visual Direction
We have a group logo currently tailored more toward telecoms, plus a separate Varnik Energy logo.
Please explore layouts that use both logos or just one, whichever works best.
Color: I wouldn't mind seeing an option using our the Blue/Purple gradient from our website (varnik-example.co.uk), but also open to non-gradient approaches and other colours..

Overall look: Smart, modern, and distinctive.
Format & Print Specs
Double-sided business card format. (Use a standard size

Must-Haves
Front: Varnik wording or Varnik Holdings wording with atleast 1 logo also on front “Business Communications | Business Energy.”

Back: Contact + company details and core products.
A design that stands out while remaining professional.

Nice-to-Have Options
A gradient version using our site’s Blue/Purple gradient.
A non-gradient version.
A dual-logo treatment versus a single-logo treatment.

Thanks
Owen

```html
<!DOCTYPE html>
<html lang="en">
<head>
<meta charset="utf-8">
<title>Varnik Holdings — Business Card</title>
<link href="https://fonts.googleapis.com/css2?family=Montserrat:wght@400;500;600;800&display=swap" rel="stylesheet">
<style>
  :root{
    --stage:#2a2a2c;
    --card:#161617;
    --card-edge:#0e0e0f;
    --emboss-light:#2b2b2d;
    --emboss-dark:#101011;
    --blue:#1fa6e0;
    --indigo:#3a4fb0;
    --navy:#2b2a7a;
    --green:#3aaa48;
    --lime:#b8cc2a;
    --white:#f2f2f2;
  }
  *{box-sizing:border-box;margin:0;padding:0}
  html,body{width:1200px;height:800px;overflow:hidden;background:var(--stage)}
  body{font-family:"Montserrat",sans-serif;position:relative}

  .card{
    position:absolute;top:102px;width:340px;height:596px;
    background:var(--card);border-radius:22px;overflow:hidden;
    box-shadow:0 0 0 1px var(--card-edge);
  }
  .card--front{left:220px}
  .card--back{left:640px}

  /* front: sideways brand block in the upper half */
  .vertical{
    position:absolute;writing-mode:vertical-rl;transform:rotate(180deg);
    white-space:nowrap;
  }
  .front-dot{
    position:absolute;left:64px;top:196px;width:100px;height:100px;border-radius:50%;
    background:linear-gradient(135deg,var(--blue),var(--indigo));
  }
  .front-wordmark{
    left:186px;top:34px;
    font-weight:800;font-size:64px;line-height:1;letter-spacing:1px;color:var(--navy);
  }
  .front-descriptor{
    left:276px;top:22px;
    font-size:13.5px;font-weight:500;line-height:1;letter-spacing:.3px;color:var(--indigo);
  }
  .front-emboss{
    position:absolute;left:30px;top:318px;width:300px;height:260px;border-radius:50%;
    background:radial-gradient(circle at 40% 40%,var(--emboss-light),var(--emboss-dark) 70%,transparent 72%);
  }

  /* back */
  .back-brand{
    position:absolute;top:46px;left:0;width:100%;
    display:flex;align-items:center;justify-content:center;gap:14px;
  }
  .back-dot{width:54px;height:54px;border-radius:50%;background:var(--green)}
  .back-wordmark{font-weight:800;font-size:46px;color:var(--navy);line-height:1}

  .person{position:absolute;top:140px;width:100%;text-align:center}
  .person-name{font-weight:800;font-size:30px;color:var(--green);line-height:1.1}
  .person-role{font-weight:500;font-size:15px;color:var(--white);margin-top:4px}

  .contact-icons{
    position:absolute;top:218px;width:100%;
    display:flex;justify-content:center;gap:12px;
  }
  .icon{
    width:30px;height:30px;border-radius:50%;
    background:linear-gradient(135deg,var(--lime),var(--green));
    display:flex;align-items:center;justify-content:center;
  }
  .icon svg{width:16px;height:16px}
  .contact-lines{
    position:absolute;top:262px;width:100%;text-align:center;
    font-size:15px;font-weight:500;color:var(--white);line-height:1.45;
  }
  .address-icon{position:absolute;top:340px;left:155px}
  .address{
    position:absolute;top:380px;width:100%;text-align:center;
    font-size:15px;font-weight:500;color:var(--white);line-height:1.4;
  }

  .band{position:absolute;left:0;bottom:0;width:100%;height:200px}
  .services{
    position:absolute;left:36px;bottom:34px;
    list-style:none;font-size:17px;font-weight:500;line-height:1.35;
  }
  .services li{
    background:linear-gradient(90deg,var(--green),var(--lime));
    -webkit-background-clip:text;background-clip:text;color:transparent;
  }
</style>
</head>
<body>

<section class="card card--front" aria-label="Card front">
  <span class="front-dot"></span>
  <span class="vertical front-wordmark">VARNIK</span>
  <span class="vertical front-descriptor">Business Communications | Business Energy</span>
  <div class="front-emboss" role="img" aria-label="Large embossed brand symbol in dark spot gloss"></div>
</section>

<section class="card card--back" aria-label="Card back">
  <div class="back-brand">
    <span class="back-dot"></span>
    <span class="back-wordmark">VARNIK</span>
  </div>

  <div class="person">
    <p class="person-name">Mira Kovalen</p>
    <p class="person-role">Founder &amp; CEO</p>
  </div>

  <div class="contact-icons">
    <span class="icon" aria-label="Phone">
      <svg viewBox="0 0 24 24"><path fill="#fff" d="M6.6 10.8a15 15 0 0 0 6.6 6.6l2.2-2.2a1 1 0 0 1 1-.25 11.4 11.4 0 0 0 3.6.57 1 1 0 0 1 1 1V20a1 1 0 0 1-1 1A17 17 0 0 1 3 4a1 1 0 0 1 1-1h3.5a1 1 0 0 1 1 1c0 1.250.2 2.45.57 3.57a1 1 0 0 1-.25 1z"/></svg>
    </span>
    <span class="icon" aria-label="Email">
      <svg viewBox="0 0 24 24"><rect x="3" y="6" width="18" height="12" rx="1.5" fill="#fff"/><path d="M3.5 7l8.5 6 8.5-6" stroke="#3aaa48" stroke-width="1.6" fill="none"/></svg>
    </span>
    <span class="icon" aria-label="Website">
      <svg viewBox="0 0 24 24" fill="none" stroke="#fff" stroke-width="1.8"><circle cx="12" cy="12" r="8.5"/><path d="M3.5 12h17M12 3.5c3 3 3 14 0 17M12 3.5c-3 3-3 14 0 17"/></svg>
    </span>
  </div>

  <p class="contact-lines">
    +44 0100 555 0199<br>
    www.varnik-example.co.uk<br>
    info@varnik-example.co.uk
  </p>

  <span class="icon address-icon" aria-label="Address">
    <svg viewBox="0 0 24 24"><path fill="#fff" d="M12 2a7 7 0 0 0-7 7c0 5 7 13 7 13s7-8 7-13a7 7 0 0 0-7-7zm0 9.5A2.5 2.5 0 1 1 12 6.5a2.5 2.5 0 0 1 0 5z"/></svg>
  </span>

  <p class="address">
    24 Example Row, Northfield,<br>
    England, NX1 2AB
  </p>

  <svg class="band" viewBox="0 0 340 200" preserveAspectRatio="none" aria-hidden="true">
    <defs>
      <linearGradient id="bandShade" x1="0" y1="0" x2="0" y2="1">
        <stop offset="0" stop-color="#232325"/>
        <stop offset="1" stop-color="#141415"/>
      </linearGradient>
    </defs>
    <path d="M0 70 C120 72 260 40 340 0 V200 H0 Z" fill="url(#bandShade)"/>
    <path d="M0 150 C140 140 260 100 340 60 V200 H0 Z" fill="#171718"/>
  </svg>

  <ul class="services">
    <li>Internet</li>
    <li>Telephony</li>
    <li>Business Mobile</li>
    <li>Business Energy Solutions</li>
  </ul>
</section>

</body>
</html>
```